Business Card Design Project

Industry/Entity Type

Business

Contact Information for Business Card

The Ardenfield Gospel Choir
Desmond Fairley, Minister of Music

The Grace Harbor Fellowship of Mount Orla
Founded 1792

Twitter @ardenfieldchoir
Instagram ardenfieldgc
Facebook socialhub-net.com/afgc382
Website: ardenfieldgc.org
For Bookings: (555) 274-AFGC
2748 Merrow Street, Marrowfield, PA 10482

Back of the Card
Music and Cd's Recordings Available On
Choirs Website and Also
Tunevault, Corvex Sound, Disc Sprout (the music online logo)

```html
<!DOCTYPE html>
<html lang="en">
<head>
<meta charset="utf-8">
<title>The Ardenfield Gospel Choir – Business Card</title>
<link rel="stylesheet" href="https://fonts.googleapis.com/css2?family=Cormorant+Garamond:ital,wght@1,600&family=Roboto:wght@400;500&family=Roboto+Condensed:wght@400;700&display=swap">
<style>
  :root {
    --backdrop: #2a2a2a;
    --choir-blue: #1f68ab;
    --choir-blue-deep: #155a98;
    --choir-red: #c8313a;
    --card-white: #f3f3f2;
    --ink-grey: #555555;
    --rule-grey: #a9a9a9;
  }
  * { box-sizing: border-box; margin: 0; padding: 0; }
  html, body { width: 1200px; height: 960px; overflow: hidden; }
  body { background: var(--backdrop); position: relative; font-family: "Roboto", sans-serif; }

  .card { position: absolute; left: 320px; width: 600px; border-radius: 20px; overflow: hidden; }

  /* Back of card */
  .card-back { top: 108px; height: 340px; background: var(--choir-blue); color: #fff; text-align: center; }
  .back-mark {
    position: absolute; left: 248px; top: 52px; width: 104px; height: 132px;
    display: flex; align-items: center; justify-content: center;
    font-family: "Roboto Condensed", sans-serif; font-weight: 700; font-size: 17px; color: #ffffff;
  }
  .back-message {
    position: absolute; left: 0; right: 0; top: 208px;
    font-family: "Cormorant Garamond", serif; font-style: italic; font-weight: 600;
    font-size: 21px; line-height: 27px;
  }
  .store-links { position: absolute; left: 0; right: 0; top: 268px; display: flex; justify-content: center; gap: 6px; }
  .store-badge {
    width: 76px; height: 30px; border: 1.5px solid #ffffff; border-radius: 15px;
    display: flex; align-items: center; justify-content: center;
    font-family: "Roboto", sans-serif; font-weight: 500; font-size: 11px; color: #ffffff;
  }

  /* Front of card */
  .card-front { top: 493px; height: 342px; background: var(--card-white); }
  .front-mark {
    position: absolute; left: 265px; top: 37px; width: 80px; height: 98px;
    display: flex; align-items: center; justify-content: center;
    font-family: "Roboto Condensed", sans-serif; font-weight: 700; font-size: 13px; color: var(--choir-red);
  }
  .choir-identity { position: absolute; left: 356px; top: 46px; width: 210px; text-align: center; }
  .choir-name {
    font-family: "Cormorant Garamond", serif; font-style: italic; font-weight: 600;
    font-size: 20px; line-height: 22px; color: var(--choir-red); text-align: left; white-space: nowrap;
  }
  .choir-director { font-weight: 500; font-size: 13px; color: var(--choir-blue); margin-top: 3px; white-space: nowrap; }
  .choir-church, .choir-founded {
    font-family: "Roboto Condensed", sans-serif; font-size: 11.5px; color: var(--ink-grey); line-height: 14px;
  }
  .choir-church { margin-top: 5px; white-space: nowrap; }

  .person { position: absolute; left: 32px; top: 150px; }
  .person-name { font-family: "Roboto Condensed", sans-serif; font-weight: 700; font-size: 24px; color: var(--choir-red); line-height: 28px; }
  .person-role { font-weight: 500; font-size: 14.5px; color: var(--choir-blue); letter-spacing: 0.3px; }

  .divider { position: absolute; left: 32px; right: 33px; top: 204px; height: 1px; background: var(--rule-grey); }

  .contact-list { position: absolute; left: 33px; top: 215px; list-style: none; }
  .contact-item { display: flex; align-items: center; gap: 8px; height: 19px; font-size: 14.5px; color: var(--ink-grey); }
  .contact-icon { width: 14px; height: 14px; flex: none; }

  .address { position: absolute; right: 32px; top: 274px; text-align: right; font-size: 14.5px; line-height: 19px; color: var(--ink-grey); }

  .stripe-red { position: absolute; left: 0; right: 0; bottom: 12px; height: 3px; background: var(--choir-red); }
  .stripe-blue { position: absolute; left: 0; right: 0; bottom: 0; height: 10px; background: var(--choir-blue-deep); }
</style>
</head>
<body>

<section class="card card-back" aria-label="Back of business card">
  <div class="back-mark">Ardenfield</div>
  <p class="back-message">Music and Cd's Recordings Available On<br>Choirs Website and Also</p>
  <div class="store-links">
    <span class="store-badge">Tunevault</span>
    <span class="store-badge">Corvex Sound</span>
    <span class="store-badge">Disc Sprout</span>
  </div>
</section>

<section class="card card-front" aria-label="Front of business card">
  <div class="front-mark">Ardenfield</div>
  <div class="choir-identity">
    <p class="choir-name">The Ardenfield Gospel Choir</p>
    <p class="choir-director">Desmond Fairley, Minister of Music</p>
    <p class="choir-church">The Grace Harbor Fellowship of Mount Orla</p>
    <p class="choir-founded">Founded 1792</p>
  </div>

  <div class="person">
    <p class="person-name">JORDAN AVERY</p>
    <p class="person-role">CEO/FOUNDER</p>
  </div>

  <div class="divider"></div>

  <ul class="contact-list">
    <li class="contact-item">
      <svg class="contact-icon" viewBox="0 0 14 14"><rect x="1" y="1" width="12" height="12" rx="2" fill="var(--choir-red)"/></svg>
      @ardenfieldchoir
    </li>
    <li class="contact-item">
      <svg class="contact-icon" viewBox="0 0 14 14"><rect x="1" y="1" width="12" height="12" rx="2" fill="var(--choir-red)"/></svg>
      ardenfieldgc
    </li>
    <li class="contact-item">
      <svg class="contact-icon" viewBox="0 0 14 14"><rect x="1" y="1" width="12" height="12" rx="2" fill="var(--choir-red)"/></svg>
      /afgc382
    </li>
    <li class="contact-item">
      <svg class="contact-icon" viewBox="0 0 14 14"><path d="M3.2 1.5l2 2.3-1 1.5c.8 1.7 2 2.9 3.6 3.7l1.5-1 2.3 2-1.2 2C6 11.6 2.3 7.9 1.2 3z" fill="var(--choir-red)"/></svg>
      (555) 274-AFGC (Bookings)
    </li>
    <li class="contact-item">
      <svg class="contact-icon" viewBox="0 0 14 14"><circle cx="7" cy="7" r="6" fill="var(--choir-red)"/><path d="M1.5 7h11M7 1v12M7 1c-3 3-3 9 0 12M7 1c3 3 3 9 0 12" stroke="#fff" stroke-width="0.9" fill="none"/></svg>
      www.ardenfieldgc.org
    </li>
  </ul>

  <p class="address">2748 Merrow Street<br>Marrowfield, PA 10482</p>

  <div class="stripe-red"></div>
  <div class="stripe-blue"></div>
</section>

</body>
</html>
```